Detail Shop Business card design

i need a business card design for my new detailing company called 'Brisk's Polish Works'. i want an all black and white design . simple, direct and to the point. i want the designer to choose a fitting font to match the logothe front should have logo, address, phone and email and the back side should have a slogan and text indicating that we offer services on anything including cars, trucks, motorcycles and RVs. slogan will read "we take pride in your ride"
maybe also very small on the back side the IG icon with Brisks_Polish_Works

phone 208.417.6352
address 3847 E Larkin Ave
Spokane WA 99214
email: BrisksPolish@mailvexo.com

Target Market(s)

all ages , auto enthusiasts

Industry/Entity Type

Automotive

Contact Information for Business Card

the front should have logo, address, phone and email and the back side should have a slogan and text indicating that we offer services on anything including cars, trucks, motorcycles and RVs. slogan will read "we take pride in your ride"

phone 208.417.6352
address 3847 E Larkin Ave
Spokane WA 99214

Colors
000000
ffffff

Requirements
Must have
• bold font and very simple design with good spacing
Nice to have
• anything creative from the designer indicating we service any types of vehicles
Should not have
• any colors ,

```html
<!DOCTYPE html>
<html lang="en">
<head>
<meta charset="utf-8">
<title>Brisk's Polish Works – Business Card</title>
<link rel="stylesheet" href="https://fonts.googleapis.com/css2?family=Roboto+Slab:wght@400;700;800&display=swap">
<style>
  :root {
    --ink: #000000;
    --paper: #ffffff;
    --stage: #e6e6e6;
    --card-black: #0d0d0d;
    --rule-light: #cfcfcf;
    --rule-dark: #3a3a3a;
  }
  * { margin: 0; padding: 0; box-sizing: border-box; }
  html, body { width: 1200px; height: 912px; overflow: hidden; }
  body {
    background: var(--stage);
    font-family: "Roboto Slab", Georgia, serif;
    display: flex;
    flex-direction: column;
    align-items: center;
    justify-content: center;
    gap: 56px;
  }
  .card {
    width: 640px;
    height: 366px;
    border-radius: 22px;
    display: flex;
    flex-direction: column;
    align-items: center;
    justify-content: center;
    box-shadow: 0 6px 18px rgba(0,0,0,0.18);
  }
  .card--back { background: var(--card-black); color: var(--paper); }
  .card--front { background: var(--paper); color: var(--ink); }

  .brand {
    display: flex;
    align-items: center;
    gap: 12px;
    font-weight: 700;
    font-size: 30px;
    letter-spacing: 0.5px;
  }
  .brand__dot {
    width: 18px; height: 18px;
    border-radius: 50%;
    background: currentColor;
  }

  .slogan {
    margin-top: 46px;
    display: flex;
    align-items: center;
    gap: 14px;
    font-size: 17px;
    letter-spacing: 1.5px;
    text-transform: uppercase;
  }
  .slogan__rule { width: 60px; height: 1px; background: var(--rule-light); }
  .services {
    margin-top: 14px;
    font-size: 19px;
    letter-spacing: 1.5px;
    text-transform: uppercase;
  }

  .person { margin-top: 30px; text-align: center; }
  .person__name {
    font-weight: 800;
    font-size: 34px;
    letter-spacing: 1.5px;
    text-transform: uppercase;
  }
  .person__role { font-size: 14px; margin-top: 2px; }
  .person__rule { width: 110px; height: 1px; background: var(--ink); margin: 10px auto 0; }

  .contact {
    margin-top: 20px;
    font-size: 15px;
    line-height: 1.75;
    text-align: center;
  }
</style>
</head>
<body>
  <section class="card card--back">
    <div class="brand"><span class="brand__dot"></span>Brisk's Polish Works</div>
    <p class="slogan"><span class="slogan__rule"></span>We take pride in your ride<span class="slogan__rule"></span></p>
    <p class="services">Cars - Trucks - Motorcycles and RVs</p>
  </section>

  <section class="card card--front">
    <div class="brand"><span class="brand__dot"></span>Brisk's Polish Works</div>
    <div class="person">
      <h1 class="person__name">Daniel Varga</h1>
      <p class="person__role">Director</p>
      <div class="person__rule"></div>
    </div>
    <div class="contact">
      <p>P : 208.417.6352 | E : BrisksPolish@mailvexo.com</p>
      <p>W : www.BrisksPolish.com | A : 3847 E Larkin Ave Spokane WA 99214</p>
    </div>
  </section>
</body>
</html>
```